Web Design Project for a beach town business owner who supports new families with their babies.

I'm looking for a basic website with the following pages: home, about, services, FAQs, blog, and contact page. I have images and content ready to go.

Target Market(s)

Men and women between the ages of 22 and 42, growing families

Industry/Entity Type

Postpartum Doula

Coding

Number of Pages Required

Font styles to use
Serif
Other font styles liked:
• My logo font is "Nexa Bold" - so coordinating fonts with that are ideal

Colors
00AB8E
00BBA5
67D7C9
C6EFE9
E9F9F6
EE7325
F08F49
F5BC92
FAE3D3
FDF4ED

Requirements
Must have
• Warm and professional vibe, multicultural images, aligned with my branding colors and font ("Nexa Bold"; COLORS: light blue hex: #2FCEC2 R: 47 G: 206 B: 194 dark blue hex: #007C7C R: 0 G: 124 B: 124 orange hex: #F77B4E R: 247 G: 123 B: 78), good SEO
Should not have
• Ultra feminine images, baby bottles, cutesy images.

```html
<!DOCTYPE html>
<html lang="en">
<head>
<meta charset="utf-8">
<title>Harbor Haven Families – Postpartum Care</title>
<meta name="description" content="Certified postpartum care and education for families of all varieties in the greater San Diego area.">
<link href="https://fonts.googleapis.com/css2?family=Montserrat:wght@300;400;500;600;700&family=Quicksand:wght@400;500;600&display=swap" rel="stylesheet">
<style>
:root{
  --teal:#1ba58a;
  --teal-dark:#148a73;
  --orange:#ec8049;
  --orange-btn:#ef7d4a;
  --ink:#3a3a3a;
  --muted:#5e5e5e;
  --dark:#2a2a2a;
  --white:#ffffff;
  --paper:#e9e9e9;
}
*{box-sizing:border-box;margin:0;padding:0}
html,body{width:1200px;height:4148px;overflow:hidden}
body{position:relative;background:var(--white);font-family:"Quicksand",sans-serif;color:var(--ink)}
.abs{position:absolute}
.heading{font-family:"Montserrat",sans-serif;font-weight:500;letter-spacing:.5px}
.btn{position:absolute;display:flex;align-items:center;justify-content:center;background:var(--orange-btn);color:var(--white);font-family:"Montserrat",sans-serif;font-weight:500;font-size:15px;border-radius:30px;letter-spacing:.3px}

/* hero */
.hero{left:0;top:0;width:1200px;height:773px;background:radial-gradient(ellipse at 50% 40%,#6b5f55 0%,#3d3631 55%,#221e1b 100%)}
.hero-shade{left:0;top:0;width:1200px;height:773px;background:rgba(0,0,0,.25)}
.brand{left:112px;top:34px;display:flex;align-items:center;gap:10px;color:var(--teal);font-family:"Montserrat",sans-serif;font-weight:700;font-size:17px}
.brand-dot{width:14px;height:14px;border-radius:50%;background:var(--teal)}
.nav{top:43px;font-family:"Montserrat",sans-serif;font-weight:500;font-size:14px;color:var(--white)}
.nav.active{color:var(--orange)}
.hero-title{left:0;width:1200px;top:350px;text-align:center;color:var(--white);font-size:68px;font-weight:600}
.hero-sub{left:0;width:1200px;top:440px;text-align:center;color:var(--white);font-size:52px;font-weight:500}
.hero-text{left:250px;width:700px;top:506px;text-align:center;color:var(--white);font-size:15px;line-height:29px}

/* welcome */
.welcome-title{left:0;width:1200px;top:848px;text-align:center;font-size:31px;color:var(--teal)}
.welcome-title span{color:var(--orange)}
.body-copy{font-size:13.5px;line-height:27px;color:var(--muted)}
.welcome-text{left:111px;top:963px;width:450px}
.welcome-text p{margin-bottom:20px}
.photo-back{left:583px;top:925px;width:483px;height:380px;background:var(--paper)}
.photo-portrait{left:599px;top:942px;width:484px;height:381px;background:linear-gradient(135deg,#55723a 0%,#8ba25c 40%,#2d87b8 75%,#1b6f9c 100%)}
.welcome-note{left:113px;top:1348px;width:970px;text-align:center}

/* key areas */
.key-photo{left:0;top:1508px;width:600px;height:514px;background:linear-gradient(160deg,#8b7a58 0%,#b9ad90 45%,#6a6150 100%)}
.key-panel{left:600px;top:1508px;width:600px;height:514px;background:var(--orange)}
.key-title{left:631px;top:1544px;font-size:42px;color:var(--white)}
.key-list{left:631px;top:1607px;width:535px;list-style:none;color:var(--white);font-size:13.5px;line-height:29px}
.key-list li{position:relative;padding-left:22px;margin-bottom:18px}
.key-list li svg{position:absolute;left:0;top:8px}
.key-list b{font-weight:600}

/* who */
.who{left:0;top:2022px;width:1200px;height:443px;background:var(--teal)}
.who-title{left:0;width:1200px;top:2088px;text-align:center;font-size:42px;color:var(--white)}
.who-text{left:190px;width:820px;top:2149px;text-align:center;color:var(--white);font-size:14.5px;line-height:29px}
.who-text p{margin-bottom:19px}
.who-text b{font-weight:600}

/* services */
.services-title{left:0;width:1200px;top:2543px;text-align:center;font-size:42px;color:var(--orange)}
.svc-photo{top:2611px;width:430px;height:323px}
.svc-photo.a{left:163px;background:linear-gradient(140deg,#8a7f74 0%,#c9c3bb 50%,#7c6f64 100%)}
.svc-photo.b{left:609px;background:linear-gradient(140deg,#9a9088 0%,#d8d2c9 50%,#8e847a 100%)}
.svc-head{top:2953px;width:420px;font-family:"Montserrat",sans-serif;font-weight:500;font-size:14.5px;line-height:27px;color:var(--dark)}
.svc-fee{top:2990px;width:420px;font-family:"Montserrat",sans-serif;font-weight:500;font-size:13px;line-height:22px;color:var(--dark)}
.svc-text{top:3018px;width:425px}

/* contact */
.contact{left:0;top:3277px;width:1200px;height:800px;background:linear-gradient(180deg,#2e2e2e 0%,#262626 100%)}
.contact-title{left:0;width:1200px;top:3335px;text-align:center;font-size:42px;color:var(--orange)}
.field{position:absolute;border:1px solid #d9d9d9;border-radius:4px;color:var(--white);font-family:"Montserrat",sans-serif;font-weight:500;font-size:13.5px;padding:0 13px;display:flex;align-items:center;justify-content:space-between}
.field.area{align-items:flex-start;padding-top:18px}
.submit{left:482px;top:3958px;width:256px;height:52px;background:var(--teal);font-size:19px}

/* footer */
.footer{left:0;top:4077px;width:1200px;height:71px;background:var(--orange)}
.foot-link{top:4106px;font-family:"Montserrat",sans-serif;font-weight:500;font-size:13.5px;color:var(--white)}
.copyright{left:875px;top:4108px;font-family:"Montserrat",sans-serif;font-size:12.5px;color:var(--white)}
</style>
</head>
<body>

<header>
  <div class="abs hero" role="img" aria-label="Photo of the caregiver with a family and their newborn on a sofa"></div>
  <div class="abs hero-shade"></div>
  <div class="abs brand"><span class="brand-dot"></span>Harbor Haven Families</div>
  <nav>
    <span class="abs nav active" style="left:435px">HOME</span>
    <span class="abs nav" style="left:507px">ABOUT</span>
    <span class="abs nav" style="left:588px">SERVICES</span>
    <span class="abs nav" style="left:688px">FAQS</span>
    <span class="abs nav" style="left:757px">BLOG</span>
    <span class="abs nav" style="left:826px">CONTACT</span>
  </nav>
  <span class="btn" style="left:934px;top:27px;width:153px;height:50px;font-size:14px">BOOK NOW</span>
  <h1 class="abs heading hero-title">HARBOR HAVEN FAMILIES</h1>
  <h2 class="abs heading hero-sub">POSTPARTUM CARE</h2>
  <p class="abs hero-text">Hi, I'm Lena Marsh, a certified postpartum care expert and educator serving families of all varieties in the greater San Diego area and beyond</p>
  <span class="btn" style="left:511px;top:575px;width:179px;height:50px">GET STARTED</span>
</header>

<section>
  <h2 class="abs heading welcome-title">WELCOME TO <span>HARBOR HAVEN FAMILIES</span></h2>
  <div class="abs body-copy welcome-text">
    <p>Congratulations on your birth and welcome to Harbor Haven Families Postpartum Care!</p>
    <p>Hi, I'm Lena Marsh, a certified postpartum care expert and educator serving families of all varieties in the greater San Diego area and beyond</p>
    <p>My passion as a professional is showing new parents just like you that whether you've just had your first child or your fifth, you can not only survive your postpartum period (also known as the 4th trimester), but you and your family can THRIVE – with the kind of compassionate, skilled, and targeted support for your unique needs that only an expert can provide. That's where I come in</p>
  </div>
  <div class="abs photo-back"></div>
  <div class="abs photo-portrait" role="img" aria-label="Portrait of the caregiver outdoors in a blue top"></div>
  <p class="abs body-copy welcome-note">Did you know that, on average, new parents won't see their midwife or obstetrician until 6 weeks after giving birth to their baby(ies)? Working with a postpartum care expert (also known as a doula) can help fill in this gap in continuity of care by providing individualized support for parents and families as they transition to life with their new baby</p>
</section>

<section>
  <div class="abs key-photo" role="img" aria-label="Photo of two parents and their child smiling by a tree"></div>
  <div class="abs key-panel"></div>
  <h2 class="abs heading key-title">KEY AREAS</h2>
  <ul class="abs key-list">
    <li><svg width="14" height="14" viewBox="0 0 14 14"><circle cx="7" cy="7" r="7" fill="#fff"/><path d="M3.8 7.2l2.2 2.2 4.2-4.4" fill="none" stroke="#ec8049" stroke-width="1.8"/></svg>I enhance <b>bonding and attachment</b> between parents(s) and baby in the areas of feeding, soothing, learning baby's cues, babywearing, and playing with baby.</li>
    <li><svg width="14" height="14" viewBox="0 0 14 14"><circle cx="7" cy="7" r="7" fill="#fff"/><path d="M3.8 7.2l2.2 2.2 4.2-4.4" fill="none" stroke="#ec8049" stroke-width="1.8"/></svg>I provide <b>practical, evidence-based information</b> about baby care and help identify what is normal and what is outside the range of normal for parent(s) and baby</li>
    <li><svg width="14" height="14" viewBox="0 0 14 14"><circle cx="7" cy="7" r="7" fill="#fff"/><path d="M3.8 7.2l2.2 2.2 4.2-4.4" fill="none" stroke="#ec8049" stroke-width="1.8"/></svg>I prioritize the <b>mental and emotional health</b> of parent(s) and help identify potential warning signs that indicate that medical care may be needed.</li>
    <li><svg width="14" height="14" viewBox="0 0 14 14"><circle cx="7" cy="7" r="7" fill="#fff"/><path d="M3.8 7.2l2.2 2.2 4.2-4.4" fill="none" stroke="#ec8049" stroke-width="1.8"/></svg>I offer <b>hands-on support</b> with baby(ies), older siblings, pets, and light home upkeep and meal preparation</li>
  </ul>
</section>

<section>
  <div class="abs who"></div>
  <h2 class="abs heading who-title">WHO WORK WITH ME</h2>
  <div class="abs who-text">
    <p>Families who work with me report feeling more connected, happy, and informed than their parenting-veteran friends and family members – both during the time that I work with them and beyond</p>
    <p>Struggle is a normal part of growth and learning. Your postpartum period is a time for <b>healing and recovering from birth, bonding with your baby, and establishing a healthy feeding relationship in whatever way works best for your family.</b> Let me show you how to remove the struggle from this magical time!</p>
  </div>
  <span class="btn" style="left:485px;top:2336px;width:230px;height:50px">LET'S GET STARTED</span>
</section>

<section>
  <h2 class="abs heading services-title">SERVICES</h2>
  <div class="abs svc-photo a" role="img" aria-label="Photo of the caregiver with parents holding their newborn"></div>
  <div class="abs svc-photo b" role="img" aria-label="Photo of the caregiver holding twin babies"></div>
  <h3 class="abs svc-head" style="left:163px">WHAT DOES A TYPICAL POSTPARTUM CARE SHIFT LOOK LIKE?</h3>
  <p class="abs body-copy svc-text" style="left:163px;top:3018px">When I arrive, I'll wash my hands and make you a cup of tea or bring you a snack and a glass of water. We'll sit down and have a chat about how you've been feeling – physically and emotionally, we'll celebrate your successes</p>
  <span class="btn" style="left:163px;top:3141px;width:154px;height:50px;font-size:14px">READ MORE</span>
  <h3 class="abs svc-head" style="left:609px">BOOKING PROCESS</h3>
  <p class="abs svc-fee" style="left:609px">MY FEES ARE $35/HOUR FOR SINGLETONS,<br>$50/HOUR FOR TWINS, &nbsp;$65/HOUR</p>
  <p class="abs body-copy svc-text" style="left:609px;top:3045px">My service hours are Monday – Friday between 9:00am and 4:00pm. I have a 3-hour minimum and 5 hour maximum requirement for all scheduled shifts</p>
  <span class="btn" style="left:609px;top:3141px;width:154px;height:50px;font-size:14px">READ MORE</span>
</section>

<section>
  <div class="abs contact"></div>
  <h2 class="abs heading contact-title">CONTACT ME</h2>
  <div class="field" style="left:168px;top:3417px;width:418px;height:61px">Name</div>
  <div class="field" style="left:614px;top:3417px;width:419px;height:61px">Email</div>
  <div class="field" style="left:168px;top:3496px;width:418px;height:61px">Phone</div>
  <div class="field" style="left:614px;top:3496px;width:419px;height:61px">Have you had your baby(ies), yet?<svg width="12" height="12"><rect x="1" y="1" width="10" height="10" fill="none" stroke="#fff" stroke-width="1.4"/></svg></div>
  <div class="field" style="left:168px;top:3578px;width:418px;height:61px">If so, did you have a birth canal or a surgical birth?<svg width="12" height="8"><path d="M0 1h12L6 7z" fill="#fff"/></svg></div>
  <div class="field" style="left:614px;top:3578px;width:419px;height:61px">If not, what is your EDD?<svg width="14" height="14"><rect x="1" y="2.5" width="12" height="10.5" fill="none" stroke="#fff" stroke-width="1.2"/><path d="M1 5.5h12M4 1v3M10 1v3M3.5 8h2M6.5 8h2M9.5 8h1.5M3.5 10.5h2M6.5 10.5h2" stroke="#fff" stroke-width="1.2"/></svg></div>
  <div class="field" style="left:168px;top:3663px;width:418px;height:62px">Is this your first baby?<svg width="12" height="12"><rect x="1" y="1" width="10" height="10" fill="none" stroke="#fff" stroke-width="1.4"/></svg></div>
  <div class="field" style="left:614px;top:3663px;width:419px;height:62px">If not, what are the ages of your older children?</div>
  <div class="field" style="left:168px;top:3747px;width:865px;height:61px">Are you interested in in-person or virtual support?*<svg width="12" height="8"><path d="M0 1h12L6 7z" fill="#fff"/></svg></div>
  <div class="field area" style="left:168px;top:3828px;width:865px;height:103px">Type here</div>
  <span class="btn submit">SUBMIT</span>
</section>

<footer>
  <div class="abs footer"></div>
  <span class="abs foot-link" style="left:110px">HOME</span>
  <span class="abs foot-link" style="left:185px">ABOUT</span>
  <span class="abs foot-link" style="left:264px">SERVICES</span>
  <span class="abs foot-link" style="left:365px">FAQS</span>
  <span class="abs foot-link" style="left:433px">BLOG</span>
  <span class="abs foot-link" style="left:502px">CONTACT</span>
  <span class="abs copyright">© 2021 ALL RIGHTS RESERVED</span>
</footer>

</body>
</html>
```